Profesional personal website needs design and business card

I need a business card with my professional name as a logo "Dorian Vitality" for my business. I am a Wellness Coach, consultant and trainer. So it should be professional, wellness oriented and modern.

Target Market(s)

Private clients, governments, corporations. Luxury and high market.

Industry/Entity Type

Health And Wellness

Contact Information for Business Card

Dorian Vitality should be the logo

Colors

Designer to choose colors to be used in the design.

Requirements
Must have
• Dorian Vitality
• Name: Tomás Lirandel
• Wellness Coach, Consultant & Trainer.
• Website: www.dorianvitality-example.com
• Phone:
• Spain (+34) 612 480 317
• (USA) +1 (555) 610 4829
Nice to have
• The most important is the design of "Dorian Vitality", as this is going to be my personal brand logo. It should be professional, wellness, high end and actual.
Should not have
• no golds, no baroque style..

```html
<!DOCTYPE html>
<html lang="en">
<head>
<meta charset="UTF-8">
<title>Dorian Vitality – Business Card</title>
<link href="https://fonts.googleapis.com/css2?family=Lato:wght@400;700&display=swap" rel="stylesheet">
<style>
  :root {
    --forest: #0a4f2c;
    --ink: #222a33;
    --slate: #4a5058;
    --paper: #ffffff;
    --backdrop: #ededeb;
  }
  * { margin: 0; padding: 0; box-sizing: border-box; }
  html, body {
    width: 1200px; height: 1200px; overflow: hidden;
    background: var(--backdrop);
    font-family: "Lato", sans-serif;
  }
  .card {
    position: absolute;
    left: 180px; width: 840px; height: 478px;
  }
  .card-front { top: 84px; background: var(--paper); }
  .card-back { top: 640px; background: var(--forest); }

  .brand {
    position: absolute;
    display: flex; align-items: center; gap: 12px;
    font-family: "Lato", sans-serif;
    font-weight: 700;
    white-space: nowrap;
  }
  .brand-dot { border-radius: 50%; flex: none; }
  .card-front .brand {
    left: 92px; top: 214px;
    font-size: 36px; color: var(--forest);
  }
  .card-front .brand-dot { width: 22px; height: 22px; background: var(--forest); }

  .divider {
    position: absolute; left: 419px; top: 154px;
    width: 3px; height: 164px; background: var(--forest);
  }

  .details { position: absolute; left: 460px; top: 150px; }
  .person-name {
    font-size: 37px; font-weight: 700; color: var(--forest);
    line-height: 1.1; letter-spacing: -0.3px;
  }
  .person-role {
    font-size: 19px; color: var(--slate); margin-top: 4px;
  }
  .contact-list { list-style: none; margin-top: 20px; }
  .contact-list li {
    display: flex; align-items: center; gap: 10px;
    font-size: 19px; color: var(--ink);
    height: 30px;
  }
  .contact-list svg { width: 18px; height: 18px; flex: none; }
  .region { color: var(--forest); }

  .card-back .brand {
    left: 50%; top: 210px; transform: translateX(-50%);
    font-size: 50px; color: var(--paper);
  }
  .card-back .brand-dot { width: 28px; height: 28px; background: var(--paper); }
  .back-url {
    position: absolute; left: 0; right: 0; top: 424px;
    text-align: center; font-size: 19px; color: var(--paper);
    letter-spacing: 0.2px;
  }
</style>
</head>
<body>

<section class="card card-front">
  <div class="brand"><span class="brand-dot"></span>Dorian Vitality</div>
  <div class="divider"></div>
  <div class="details">
    <h1 class="person-name">Tomás Lirandel</h1>
    <p class="person-role">Wellness Coach, Consultant &amp; Trainer</p>
    <ul class="contact-list">
      <li>
        <svg viewBox="0 0 24 24" aria-hidden="true"><path fill="#0a4f2c" d="M6.6 10.8a15.1 15.1 0 0 0 6.6 6.6l2.2-2.2a1 1 0 0 1 1-.25 11.4 11.4 0 0 0 3.6.57 1 1 0 0 1 1 1V20a1 1 0 0 1-1 1A17 17 0 0 1 3 4a1 1 0 0 1 1-1h3.5a1 1 0 0 1 1 1c0 1.25.2 2.45.57 3.57a1 1 0 0 1-.25 1z"/></svg>
        <span>(+34) 612 480 317 <span class="region">Spain</span></span>
      </li>
      <li>
        <svg viewBox="0 0 24 24" aria-hidden="true"><rect x="6" y="2" width="12" height="20" rx="2" fill="none" stroke="#0a4f2c" stroke-width="2"/><circle cx="12" cy="18" r="1.3" fill="#0a4f2c"/></svg>
        <span>+1 (555) 610 4829 <span class="region">(USA)</span></span>
      </li>
      <li>
        <svg viewBox="0 0 24 24" aria-hidden="true"><circle cx="12" cy="12" r="9" fill="none" stroke="#0a4f2c" stroke-width="2"/><path d="M3 12h18M12 3c3 3 3 15 0 18M12 3c-3 3-3 15 0 18" fill="none" stroke="#0a4f2c" stroke-width="1.5"/></svg>
        <span>www.dorianvitality-example.com</span>
      </li>
    </ul>
  </div>
</section>

<section class="card card-back">
  <div class="brand"><span class="brand-dot"></span>Dorian Vitality</div>
  <p class="back-url">www.dorianvitality-example.com</p>
</section>

</body>
</html>
```